Design a compelling Tarnwove Business Card that will drive people to my site

I want a business card that I can give to people—less to tell them who I am and more to direct them to my website. My website is a portal for Pelmor Aquatics Officials and a place for people who want to become Pelmor Aquatics Officials.
I am uploading my official company logo as well as a business card mockup that I did on my own. Please feel free to completely stray from this design.
I've included a screen recording of the homepage of my website as well.
Target Market(s)
Pelmor Aquatics Officials and people who desire to become one
Contact Information for Business Card
website url
Look and feel
Each slider illustrates characteristics of the customer's brand and the style your logo design should communicate.

```html
<!DOCTYPE html>
<html lang="en">
<head>
<meta charset="utf-8">
<title>Tarnwove Business Card</title>
<link rel="stylesheet" href="https://fonts.googleapis.com/css2?family=Montserrat:wght@400;500;700&display=swap">
<style>
  :root {
    --brand-blue: #3a55a8;
    --wave-blue: #93a8d8;
    --pale-blue: #a9bbe6;
    --card-white: #ffffff;
    --page-bg: #e9eaee;
  }
  * { box-sizing: border-box; margin: 0; padding: 0; }
  html, body {
    width: 1200px; height: 912px; overflow: hidden;
    background: var(--page-bg);
    font-family: "Montserrat", sans-serif;
  }
  .card {
    position: absolute;
    width: 540px; height: 310px;
    border-radius: 16px;
    overflow: hidden;
    box-shadow: 0 10px 28px rgba(20, 30, 60, 0.22);
  }
  .card-front {
    left: 90px; top: 80px;
    background: var(--brand-blue);
    display: flex; flex-direction: column; align-items: center; justify-content: center;
  }
  .card-front .wordmark {
    color: var(--card-white);
    font-weight: 700;
    font-size: 64px;
    line-height: 1;
    letter-spacing: -1px;
  }
  .card-front .tagline {
    color: var(--card-white);
    font-weight: 400;
    font-size: 13px;
    margin-top: 26px;
    letter-spacing: 0.3px;
  }
  .card-back {
    left: 570px; top: 520px;
    background: var(--card-white);
  }
  .card-back .backdrop { position: absolute; inset: 0; width: 100%; height: 100%; }
  .card-back .wordmark {
    position: absolute; left: 50px; top: 84px;
    color: var(--brand-blue);
    font-weight: 700;
    font-size: 44px;
    line-height: 1;
    letter-spacing: -1px;
  }
  .contact {
    position: absolute; right: 30px; top: 130px;
    text-align: right;
    color: var(--card-white);
  }
  .contact .person-name {
    color: var(--pale-blue);
    font-weight: 700; font-size: 17px;
    line-height: 1.2;
  }
  .contact .person-title {
    font-weight: 500; font-size: 12px; margin-top: 2px;
  }
  .contact .divider {
    width: 16px; height: 1px; background: var(--pale-blue);
    margin: 8px 0 10px auto;
  }
  .contact-list { list-style: none; }
  .contact-list li {
    display: flex; align-items: center; justify-content: flex-end; gap: 8px;
    font-size: 12px; font-weight: 400; line-height: 22px;
  }
  .contact-list svg { width: 11px; height: 11px; fill: none; stroke: var(--card-white); stroke-width: 1.4; }
</style>
</head>
<body>
  <section class="card card-front">
    <div class="wordmark">Tarnwove</div>
    <div class="tagline">Your Lane to the Officials’ Deck</div>
  </section>

  <section class="card card-back">
    <svg class="backdrop" viewBox="0 0 540 310" preserveAspectRatio="none" aria-hidden="true">
      <path d="M0,262 C170,266 260,232 340,142 C400,76 460,60 540,56 L540,310 L0,310 Z" fill="var(--brand-blue)"/>
      <path d="M60,250 C180,258 262,222 336,134 C396,66 456,50 500,48" fill="none" stroke="var(--wave-blue)" stroke-width="6" stroke-linecap="round"/>
      <path d="M30,212 C90,238 170,236 228,206" fill="none" stroke="var(--wave-blue)" stroke-width="7" stroke-linecap="round"/>
    </svg>
    <div class="wordmark">Tarnwove</div>
    <div class="contact">
      <div class="person-name">Marcus Ellery</div>
      <div class="person-title">CEO &amp; Founder</div>
      <div class="divider"></div>
      <ul class="contact-list">
        <li>(555) 210-4738
          <svg viewBox="0 0 12 12"><path d="M2.5 1.5 L4.5 1.5 L5.2 4 L4 5 C4.7 6.5 5.5 7.3 7 8 L8 6.8 L10.5 7.5 L10.5 9.5 C6 9.8 2.2 6 2.5 1.5 Z"/></svg>
        </li>
        <li>marcus@tarnwove.com
          <svg viewBox="0 0 12 12"><rect x="1" y="2.5" width="10" height="7"/><path d="M1 2.5 L6 6.5 L11 2.5"/></svg>
        </li>
        <li>www.tarnwove.com
          <svg viewBox="0 0 12 12"><circle cx="6" cy="6" r="4.8"/><ellipse cx="6" cy="6" rx="2" ry="4.8"/><path d="M1.2 6 H10.8"/></svg>
        </li>
      </ul>
    </div>
  </section>
</body>
</html>
```